Creative, fresh business card design for Ripplecraft Facades

We need a fresh, creative business card design for Ripplecraft Facades. We are the manufacturer of Ripplecraft Facades in Australia. Wall panels are 2400 x 1200mm panels made from MDF and feature 3D patterns on the face of the panel. The colours to be used are green, silver/grey and white RGB
Red 187
Green 207
Blue 65.

An idea is to possibly use a watermark of one of our designs as a background (like on the "Grids" design on the left hand side of page 2 of our brochure).

Target Market(s)

Interior designers, architects, builders and home renovators

Industry/Entity Type

Business

Contact Information for Business Card

Details to go on the card are:
Our logo (attached),
Slogan: "Decorative panels for interiors and exteriors",
Contact name,
Position,
Mobile phone number,
Business address,
Business phone,
Business fax,
Website and
Email address.

I have attached a few images of our panels and our brochure for reference.

The colours of the business card should feature our logo colours which are: RGB
Red 187
Green 207
Blue 65

Requirements
Must have
• Very modern fonts and design. Some of the designs shown especially the "Prisms" design which is a popular design.
Nice to have
• Creative but simple design. Very contemporary.
Should not have
• Anything ornate or old fashioned.

```html
<!DOCTYPE html>
<html lang="en">
<head>
<meta charset="utf-8">
<title>Ripplecraft Facades – Business Card</title>
<link rel="stylesheet" href="https://fonts.googleapis.com/css2?family=Open+Sans:wght@400;600;700&family=Saira+Semi+Condensed:wght@700&display=swap">
<style>
  :root {
    --backdrop: #4a423d;
    --card: #111111;
    --card-edge: #1c1c1c;
    --brand-green: rgb(187, 207, 65);
    --silver: #c9c9c9;
    --grey-text: #a9a9a9;
    --light-text: #d6d6d6;
    --divider: #2a2a2a;
  }
  * { box-sizing: border-box; margin: 0; padding: 0; }
  html, body {
    width: 1200px; height: 844px; overflow: hidden;
    background: var(--backdrop);
  }
  .stage {
    position: relative; width: 1200px; height: 844px;
    display: flex; align-items: center; justify-content: center; gap: 60px;
  }
  .card {
    position: relative; width: 520px; height: 300px;
    background: var(--card);
    border: 1px solid var(--card-edge);
    overflow: hidden;
    font-family: "Open Sans", Arial, sans-serif;
  }

  /* Contact side */
  .brand-block {
    position: absolute; left: 30px; top: 118px; width: 215px;
  }
  .brand-name {
    display: flex; align-items: center; gap: 8px;
    color: var(--brand-green); font-weight: 700; font-size: 21px;
    line-height: 1; white-space: nowrap;
  }
  .brand-square {
    width: 14px; height: 14px; background: var(--brand-green); flex: none;
  }
  .brand-tagline {
    margin-top: 10px; color: var(--grey-text);
    font-size: 11px; letter-spacing: 2px; line-height: 1.35;
  }
  .divider {
    position: absolute; left: 262px; top: 34px; bottom: 34px;
    width: 1px; background: var(--divider);
  }
  .contact {
    position: absolute; left: 282px; top: 46px; right: 16px;
    color: var(--light-text); font-size: 12.5px; line-height: 1.3;
  }
  .contact-name {
    color: var(--brand-green); font-weight: 700; font-size: 18px; line-height: 1.1;
  }
  .contact-role { color: var(--grey-text); font-size: 12.5px; margin-bottom: 16px; }
  .contact-address { margin-bottom: 16px; }
  .contact-list { list-style: none; }
  .contact-list li { display: flex; align-items: center; gap: 8px; height: 17px; }
  .contact-list svg { width: 11px; height: 11px; flex: none; fill: var(--brand-green); }

  /* Logo side */
  .panel-texture {
    position: absolute; inset: 0;
    background:
      linear-gradient(135deg, #1a1a1a 0%, #121212 40%, #1b1b1b 70%, #131313 100%);
  }
  .front-mark {
    position: absolute; left: 0; right: 0; top: 92px;
    display: flex; flex-direction: column; align-items: center;
  }
  .front-name {
    display: flex; align-items: center; gap: 10px;
    color: var(--silver); font-weight: 700; font-size: 30px; line-height: 1;
  }
  .front-name .brand-square { width: 18px; height: 18px; background: var(--silver); }
  .front-slogan {
    margin-top: 26px; text-align: center;
    font-family: "Saira Semi Condensed", "Arial Narrow", sans-serif;
    color: var(--brand-green); font-size: 17px; line-height: 1.15; letter-spacing: 0.5px;
    text-transform: uppercase;
  }
</style>
</head>
<body>
<main class="stage">

  <section class="card card--contact" aria-label="Business card, contact side">
    <div class="brand-block">
      <div class="brand-name"><span class="brand-square"></span>Ripplecraft Facades</div>
      <p class="brand-tagline">decorative panels for<br>interiors &amp; landscapes</p>
    </div>
    <div class="divider"></div>
    <div class="contact">
      <p class="contact-name">Marcus Hale</p>
      <p class="contact-role">Managing Director</p>
      <p class="contact-address">48, Kestrel Lane Road<br>Brookvale, 204517.</p>
      <ul class="contact-list">
        <li><svg viewBox="0 0 12 12" aria-hidden="true"><path d="M3 0h6a1 1 0 0 1 1 1v10a1 1 0 0 1-1 1H3a1 1 0 0 1-1-1V1a1 1 0 0 1 1-1zm0 1.5v8h6v-8zM6 10a.6.6 0 1 0 0 1.2A.6.6 0 0 0 6 10z"/></svg>044-555 210 374</li>
        <li><svg viewBox="0 0 12 12" aria-hidden="true"><path d="M1 4c0-2 2-3 5-3s5 1 5 3v1H8.5V3.8h-5V5H1zM2 6h8l1 5H1zm4 1.3a1.6 1.6 0 1 0 0 3.2 1.6 1.6 0 0 0 0-3.2z"/></svg>044-555 210 375</li>
        <li><svg viewBox="0 0 12 12" aria-hidden="true"><path d="M2 0h6v3H2zM0 4h12v8H0zm2 2v1.5h8V6zm0 3v1h2V9zm3 0v1h2V9zm3 0v1h2V9z"/></svg>044-555 210 376</li>
        <li><svg viewBox="0 0 12 12" aria-hidden="true"><path d="M0 2h12v8H0zm1 1v.4l5 3.4 5-3.4V3z"/></svg>info@ripplecraft.com</li>
        <li><svg viewBox="0 0 12 12" aria-hidden="true"><path d="M6 0a6 6 0 1 0 0 12A6 6 0 0 0 6 0zm0 1.2c.7 0 1.5 1.7 1.7 4.2H4.3C4.5 2.9 5.3 1.2 6 1.2zm-4.7 4.2h1.9c.1-1.6.4-3 1-3.8A4.9 4.9 0 0 0 1.3 5.4zm0 1.2a4.9 4.9 0 0 0 2.9 3.8c-.5-.8-.9-2.2-1-3.8zm3 0h3.4C7.5 9.1 6.7 10.8 6 10.8S4.5 9.1 4.3 6.6zm4.5 0c-.1 1.6-.4 3-1 3.8a4.9 4.9 0 0 0 2.9-3.8zm1.9-1.2a4.9 4.9 0 0 0-2.9-3.8c.5.8.9 2.2 1 3.8z"/></svg>www.ripplecraftfacades.com</li>
      </ul>
    </div>
  </section>

  <section class="card card--brand" aria-label="Business card, brand side">
    <div class="panel-texture" role="img" aria-label="Faint embossed prism panel pattern across the card"></div>
    <div class="front-mark">
      <div class="front-name"><span class="brand-square"></span>Ripplecraft Facades</div>
      <p class="front-slogan">Decorative panels for<br>interiors and exteriors</p>
    </div>
  </section>

</main>
</body>
</html>
```